Gobal construction supply company needs new business card design

I need a business card design for my global supply company using an existing logo. i will be looking to print these on rounded corner cards with the black background version of my logo on the back. on the front white background, my logo again and my simple details.

```html
<!DOCTYPE html>
<html lang="en">
<head>
<meta charset="utf-8">
<title>Meridian Build Supply – Business Card</title>
<link rel="stylesheet" href="https://fonts.googleapis.com/css2?family=Montserrat:wght@600&family=Open+Sans:wght@400&display=swap">
<style>
  :root {
    --stage: #5f5f5f;
    --brand-red: #d90000;
    --ink-black: #111111;
    --card-white: #f2f2f2;
    --text-dark: #333333;
    --text-light: #ffffff;
  }
  * { margin: 0; padding: 0; box-sizing: border-box; }
  html, body { width: 1200px; height: 802px; overflow: hidden; }
  body { background: var(--stage); position: relative; }

  .card {
    position: absolute;
    top: 274px;
    width: 443px;
    height: 265px;
    border-radius: 13px;
    overflow: hidden;
    box-shadow: 0 3px 6px rgba(0,0,0,0.35);
  }
  .card--front { left: 136px; background: var(--card-white); }
  .card--back  { left: 624px; background: var(--ink-black); }

  .band { position: absolute; }
  .band--red-top    { left: 0;    top: 0;    width: 57px; height: 90px;  background: var(--brand-red); }
  .band--black-edge { left: 0;    top: 90px; width: 26px; height: 175px; background: var(--ink-black); }
  .band--red-stem   { left: 26px; top: 90px; width: 31px; height: 175px; background: var(--brand-red); }
  .band--black-col  { left: 57px; top: 0;    width: 72px; height: 265px; background: var(--ink-black); }

  .contact {
    position: absolute;
    left: 201px;
    top: 136px;
    font-family: "Open Sans", sans-serif;
    color: var(--text-dark);
  }
  .contact__name {
    font-family: "Montserrat", sans-serif;
    font-weight: 600;
    font-size: 16px;
    color: var(--brand-red);
    line-height: 18px;
    margin-left: 0;
  }
  .contact__role { font-size: 13px; line-height: 15px; margin-bottom: 8px; }
  .contact__list { list-style: none; }
  .contact__item {
    display: flex;
    align-items: center;
    font-size: 12.5px;
    line-height: 15.7px;
    margin-left: -2px;
  }
  .contact__icon { width: 10px; height: 10px; margin-right: 5px; fill: var(--brand-red); flex: none; }

  .wordmark {
    position: absolute;
    left: 0; right: 0;
    top: 116px;
    display: flex;
    justify-content: center;
    align-items: center;
    gap: 9px;
  }
  .wordmark__name {
    font-family: "Montserrat", sans-serif;
    font-weight: 600;
    font-size: 19px;
    letter-spacing: 0.5px;
    color: var(--text-light);
  }
  .wordmark__dot {
    width: 17px; height: 17px;
    border-radius: 50%;
    background: var(--brand-red);
  }
</style>
</head>
<body>
  <section class="card card--front">
    <div class="band band--red-top"></div>
    <div class="band band--black-edge"></div>
    <div class="band band--red-stem"></div>
    <div class="band band--black-col"></div>

    <div class="contact">
      <p class="contact__name">DANIEL HARPER</p>
      <p class="contact__role">Managing Director</p>
      <ul class="contact__list">
        <li class="contact__item">
          <svg class="contact__icon" viewBox="0 0 10 10" aria-hidden="true"><path d="M0 3 Q5 -1 10 3 L8 4.5 L7 3.5 Q5 2.8 3 3.5 L2 4.5 Z M2 5 H8 L9 9 H1 Z"/></svg>
          055-210 384 617
        </li>
        <li class="contact__item">
          <svg class="contact__icon" viewBox="0 0 10 10" aria-hidden="true"><path d="M2.5 0 H7.5 V10 H2.5 Z M3.5 1.2 V7.5 H6.5 V1.2 Z"/></svg>
          055-210 384 617
        </li>
        <li class="contact__item">
          <svg class="contact__icon" viewBox="0 0 10 10" aria-hidden="true"><path d="M0 2 H10 V8 H0 Z" /><path d="M0 2 L5 5.5 L10 2" stroke="#f2f2f2" stroke-width="1" fill="none"/></svg>
          hello@meridianbuild.com
        </li>
        <li class="contact__item">
          <svg class="contact__icon" viewBox="0 0 10 10" aria-hidden="true"><circle cx="5" cy="5" r="5"/><path d="M2 4 Q4 2 5 4 T8 6" stroke="#f2f2f2" stroke-width="1" fill="none"/></svg>
          www.meridianbuild.com
        </li>
      </ul>
    </div>
  </section>

  <section class="card card--back">
    <div class="wordmark">
      <span class="wordmark__name">MERIDIAN BUILD SUPPLY</span>
      <span class="wordmark__dot"></span>
    </div>
  </section>
</body>
</html>
```